Business Card Design & Gift cards, Gift Cert, Donation Card

Retail Gift Store-in addition to Business Cards we'd like sequenced 2 sided Gift cards, Gift Certificate Cards, and Donation Cards.please see examples and email for clarificationlogos attached with examples-
Gift Card, Gift Certificate and Donation Card will all be same style just differant upper right title, with back side info as example.
business card, as example is single sided.
looking for additional ideas for layout

Industry/Entity Type

Business

Contact Information for Business Card

211 Newman St.East Tawas, MI 48730989.362.8730Office@BrewKrew.com

Requirements
Must have
• Blue as per example
• Logos provided
• like gradiant background

```html
<!DOCTYPE html>
<html lang="en">
<head>
<meta charset="utf-8">
<title>Tillow Marsh – Business Card</title>
<link href="https://fonts.googleapis.com/css2?family=Arimo:wght@400&display=swap" rel="stylesheet">
<style>
  :root{
    --page-bg:#e9e9e7;
    --card-white:#ffffff;
    --card-mid:#e3f3fa;
    --wave-light:#bfe5f3;
    --wave-deep:#45b6de;
    --wave-line:#8fd3ec;
    --brand-blue:#2b40c8;
    --ink:#1a1a1a;
    --ghost:#d6d6d6;
    --icon-bg:#222222;
  }
  *{box-sizing:border-box;margin:0;padding:0}
  html,body{width:1200px;height:902px;overflow:hidden;background:var(--page-bg)}
  .stage{position:relative;width:1200px;height:902px}
  .card{
    position:absolute;left:240px;width:720px;height:411px;overflow:hidden;
    box-shadow:0 8px 24px rgba(0,0,0,.16);
    font-family:"Arimo",sans-serif;font-weight:400;
  }

  /* back side */
  .card-back{top:30px;background:var(--card-white)}
  .back-watermark{
    position:absolute;left:400px;top:40px;width:200px;height:200px;border-radius:50%;
    background:var(--ghost);opacity:.6;
  }
  .back-name{
    position:absolute;left:0;right:0;top:170px;text-align:center;
    font-size:68px;letter-spacing:2px;text-transform:uppercase;color:var(--ink);
  }

  /* front side */
  .card-front{
    top:461px;
    background:linear-gradient(180deg,var(--card-white) 0%,var(--card-white) 22%,var(--card-mid) 60%,var(--wave-light) 100%);
  }
  .card-waves{position:absolute;inset:0;width:100%;height:100%}
  .brand-mark{
    position:absolute;left:70px;top:150px;width:150px;height:150px;border-radius:50%;
    background:var(--brand-blue);
  }
  .brand-name{
    position:absolute;left:250px;top:70px;
    font-size:44px;letter-spacing:2px;text-transform:uppercase;color:var(--brand-blue);
  }
  .contact{
    position:absolute;right:36px;top:160px;list-style:none;
    font-size:15px;color:var(--ink);
  }
  .contact li{display:flex;align-items:center;justify-content:flex-end;gap:12px;height:30px}
  .contact-icon{width:18px;height:18px;border-radius:3px;background:var(--icon-bg);display:flex;align-items:center;justify-content:center}
  .contact-icon svg{width:12px;height:12px}
</style>
</head>
<body>
<div class="stage">
  <section class="card card-back">
    <div class="back-watermark"></div>
    <div class="back-name">Tillow Marsh</div>
  </section>

  <section class="card card-front">
    <svg class="card-waves" viewBox="0 0 720 411" preserveAspectRatio="none" aria-hidden="true">
      <defs>
        <linearGradient id="waveFill" x1="0" y1="0" x2="0" y2="1">
          <stop offset="0" stop-color="var(--wave-light)"/>
          <stop offset="0.45" stop-color="var(--wave-deep)"/>
          <stop offset="1" stop-color="var(--wave-deep)"/>
        </linearGradient>
      </defs>
      <path d="M0 345 C 180 315, 300 320, 400 260 C 500 200, 590 145, 720 125 L720 411 L0 411 Z" fill="url(#waveFill)"/>
      <path d="M0 322 C 170 292, 310 296, 410 238 C 520 178, 600 130, 720 113" fill="none" stroke="var(--wave-line)" stroke-width="2.5"/>
      <path d="M0 368 C 190 345, 320 343, 425 285 C 525 228, 610 172, 720 155" fill="none" stroke="#ffffff" stroke-opacity=".35" stroke-width="1.5"/>
    </svg>

    <div class="brand-mark"></div>
    <div class="brand-name">Tillow Marsh</div>

    <ul class="contact">
      <li><span>989.517.4296</span>
        <span class="contact-icon"><svg viewBox="0 0 16 16"><path d="M4 2h2l1 3-1.5 1a7 7 0 0 0 4.5 4.5L11 9l3 1v2a2 2 0 0 1-2 2A10 10 0 0 1 2 4a2 2 0 0 1 2-2z" fill="#fff"/></svg></span></li>
      <li><span>Office@TillowMarsh.com</span>
        <span class="contact-icon"><svg viewBox="0 0 16 16"><rect x="2" y="4" width="12" height="8" fill="none" stroke="#fff" stroke-width="1.5"/><path d="M2 4l6 5 6-5" fill="none" stroke="#fff" stroke-width="1.5"/></svg></span></li>
      <li><span>482 Larkfield Ave. Pine Cove, MI 48702</span>
        <span class="contact-icon"><svg viewBox="0 0 16 16"><path d="M8 1a4.5 4.5 0 0 0-4.5 4.5C3.5 9 8 15 8 15s4.5-6 4.5-9.5A4.5 4.5 0 0 0 8 1z" fill="#fff"/><circle cx="8" cy="5.5" r="1.6" fill="var(--icon-bg)"/></svg></span></li>
    </ul>
  </section>
</div>
</body>
</html>
```